Stationery Design Project

We need a stationery design for our Norwegian trucking company. We have existed for about 15 years and our 12 drivers uses relatively new vehicles to transport goods around in northern Norway. Long distance routes with fresh fish og food transport is our main operations.

We have already made alogo that's printed on our trucks. The logo and a picture of our trucks is attached. I think the logo i crappy, but since its already in use, changing it is not an option in this round. Still using a better colour scheme in the overall stationery and more interesting fonts is possible (altso in the logo).

Company details:
Name: Kjelvraket AS
Organisation nr 873 615 309
Post adress: 8642 Raudvik

I like minimalism and simplicity. I am avalibly for questions in normal GMT working hours either here or on mail: ivar@fjordlast.no

Reason: Hi. Im extending the deadline because I needed some time to find a vector file of our logo. Sorry for the inconvenience

Hi, and thanks for all your interest in the project. Some updates:

-          I have decided to commit to using one of the designs. Some designer will get the payment.

-          I have extended the deadline with 24 hours since I needed some time to find our firms vector logo (a slow Swedish man was holding me up)

-          We will not choose a design before the deadline. No need to rush.

-          We have received a lot of great design and think there is a need to specified the product we want to make:

o   Business Card for all our employers. I just need the design and will duplicate with the correct numbers and name myself. The information on should be: Logo, employer’s name, Phone number, email, website, Postal number and address. Use this as a template: logo, Leif Brattvoll, 47382066, Leif@fjordlast.no,, fjordlast.no, 8642 Raudvik. The order and placement of the information is your creative decision.

o   Stickers to put on the goods we travel. On the sticker the should be the following information: Logo, phone number, Tekst and link: Fraktæ av Kjelvraket. Ke du syns? Fjordlast.no/tilbakemelding (this means: Handled by Kjelvraket. What do you think Fjordlast.no/feedback -à the link will be a feedback form). The placement the information and size is your creative decision with some stings: we have been thinking of using Drukko for printing and see that a size about 6x6 cm, 8x5 or something like that. (with 3000 copies our budget is 200 punds). Any suggestions of other suppliers are welcome. Drukko price calculator http://www.drukkolabelhouse.co.uk/digital-litho-printing/printing-labels-tags/stickers/

o   Letterhead with logo, address, phone number and organizational number.

o   Envelopes with logo,address, phone number and organizational number.

Have a nice day.

 

 

• Using the blue colour in the logo and using a similar graphic approch.

```html
<!DOCTYPE html>
<html lang="no">
<head>
<meta charset="utf-8">
<title>Kjelvraket – business cards</title>
<link href="https://fonts.googleapis.com/css2?family=Open+Sans:wght@400;600;700&display=swap" rel="stylesheet">
<style>
  :root {
    --backdrop: #8d9196;
    --paper: #ffffff;
    --navy: #0a4ea3;
    --blue: #0072bc;
    --sky: #2a8fd6;
    --ink: #222a33;
  }
  * { box-sizing: border-box; margin: 0; padding: 0; }
  html, body { width: 1200px; height: 732px; overflow: hidden; }
  body {
    position: relative;
    background: var(--backdrop);
    font-family: "Open Sans", Arial, sans-serif;
  }
  .card {
    position: absolute;
    width: 519px;
    height: 296px;
    overflow: hidden;
  }
  .card--front { left: 64px; top: 43px; background: var(--paper); box-shadow: 0 0 0 1px #c9ccd0; }
  .card--back-white { left: 617px; top: 43px; background: var(--paper); box-shadow: 0 0 0 1px #c9ccd0; }
  .card--back-blue { left: 64px; top: 386px; background: var(--blue); }
  .card--back-navy { left: 617px; top: 382px; background: var(--navy); }

  .wordmark {
    position: absolute;
    display: flex;
    align-items: center;
    gap: 14px;
    font-weight: 700;
    font-size: 42px;
    letter-spacing: 0.5px;
    color: var(--navy);
  }
  .wordmark__dot {
    width: 22px; height: 22px; border-radius: 50%;
    background: currentColor;
  }
  .wordmark--light { color: #ffffff; }
  .card--back-white .wordmark,
  .card--back-blue .wordmark,
  .card--back-navy .wordmark { left: 0; right: 0; top: 122px; justify-content: center; }
  .card--front .wordmark { left: 34px; top: 58px; }

  .web {
    position: absolute; left: 0; right: 0; top: 246px;
    text-align: center;
    font-size: 17px;
    letter-spacing: 4px;
    color: var(--ink);
  }
  .web--light { color: #ffffff; }

  .contact-band {
    position: absolute; left: 240px; top: 190px;
    width: 279px; height: 106px;
    background: linear-gradient(135deg, var(--sky) 0%, var(--navy) 60%);
  }

  .holder {
    position: absolute; left: 33px; top: 176px;
    font-weight: 700; font-size: 20px; color: var(--navy);
  }
  .postal {
    position: absolute; left: 33px; top: 214px;
    display: flex; align-items: center; gap: 5px;
    font-size: 13px; color: var(--ink);
  }
  .contact {
    position: absolute; right: 12px; top: 204px;
    list-style: none; text-align: right;
    font-size: 13.5px; line-height: 20px; color: #ffffff;
  }
  .contact li { display: flex; justify-content: flex-end; align-items: center; gap: 5px; }
  .contact svg { width: 10px; height: 10px; fill: #ffffff; }
</style>
</head>
<body>

  <section class="card card--front" aria-label="Business card front">
    <div class="contact-band" role="img" aria-label="Blue wave band decoration"></div>

    <div class="wordmark"><span class="wordmark__dot"></span>Kjelvraket</div>

    <p class="holder">Leif Brattvoll</p>
    <p class="postal">
      <svg width="11" height="10" viewBox="0 0 11 10" aria-hidden="true"><path d="M5.5 0 L11 4.5 H9.5 V10 H1.5 V4.5 H0 Z" fill="var(--ink)"/></svg>
      8642 Raudvik
    </p>

    <ul class="contact">
      <li><svg viewBox="0 0 10 10" aria-hidden="true"><path d="M2 0 L4 2.5 L3 3.8 C3.6 5.2 4.8 6.4 6.2 7 L7.5 6 L10 8 L8.8 9.8 C4 9.5 0.5 6 0.2 1.2 Z"/></svg>47382066</li>
      <li>Org nr 873 615 309</li>
      <li><svg viewBox="0 0 10 10" aria-hidden="true"><path d="M0 2 H10 V9 H0 Z M0 2 L5 6 L10 2" stroke="var(--navy)" stroke-width="0.8"/></svg>Leif@fjordlast.no</li>
      <li><svg viewBox="0 0 10 10" aria-hidden="true"><circle cx="5" cy="5" r="4.5"/><path d="M0.5 5 H9.5 M5 0.5 V9.5 M5 0.5 C2.5 3 2.5 7 5 9.5 M5 0.5 C7.5 3 7.5 7 5 9.5" stroke="var(--navy)" stroke-width="0.7" fill="none"/></svg>www.fjordlast.no</li>
    </ul>
  </section>

  <section class="card card--back-white" aria-label="Business card back, white">
    <div class="wordmark"><span class="wordmark__dot"></span>Kjelvraket</div>
    <p class="web">www.fjordlast.no</p>
  </section>

  <section class="card card--back-blue" aria-label="Business card back, blue">
    <div class="wordmark wordmark--light"><span class="wordmark__dot"></span>Kjelvraket</div>
    <p class="web web--light">www.fjordlast.no</p>
  </section>

  <section class="card card--back-navy" aria-label="Business card back, navy">
    <div class="wordmark wordmark--light"><span class="wordmark__dot"></span>Kjelvraket</div>
    <p class="web web--light">www.fjordlast.no</p>
  </section>

</body>
</html>
```